Webdesign für Branchenverzeichnis
Zielgruppe
Wir-bauen-Brücken – das Branchenverzeichnis der Selbstverantwortlichen.
Der Anbieter präsentiert sich mit seinem Namen und der URL - ähnlich wie bei 'blaue Tafeln' oder Jobkranich.
Aufgabenstellung
Das Branchenverzeichnis sollte neutral und gleichzeitig hochwertig sein. Die Hauptfarben sind Gold, Schwarz und Weiß. Logo und Corporate Design wurden bereits entwickelt

```html
<!DOCTYPE html>
<html lang="de">
<head>
<meta charset="utf-8">
<title>Wir-bauen-Brücken – Branchenverzeichnis</title>
<link href="https://fonts.googleapis.com/css2?family=Quicksand:wght@400;500;600;700&display=swap" rel="stylesheet">
<style>
:root{
  --gold:#d5b062;
  --gold-soft:#e8d49b;
  --gold-text:#d3ae5f;
  --cream:#fbf3d3;
  --card-active:#fffce8;
  --hero-bg:#fafafa;
  --ink:#111;
  --grey:#777;
  --dark:#3a3a3a;
  --white:#fff;
}
*{box-sizing:border-box;margin:0;padding:0}
html,body{width:1088px;height:1200px;overflow:hidden}
body{position:relative;font-family:'Quicksand',sans-serif;color:var(--ink);background:var(--cream)}

/* header */
.site-header{position:absolute;left:0;top:0;width:1088px;height:57px;background:linear-gradient(#6b6b6b,#3c3c3c);z-index:3}
.brand{position:absolute;left:143px;top:19px;display:flex;align-items:center;gap:5px;color:var(--gold);font-weight:600;font-size:8.5px;white-space:nowrap}
.brand-dot{width:18px;height:18px;border-radius:50%;border:2px solid var(--gold);flex:none}
.nav a{position:absolute;top:23px;color:var(--white);font-size:8.2px;font-weight:700;letter-spacing:1.1px;text-decoration:none}
.nav a.active{color:var(--gold)}
.icon-box{position:absolute;top:17px;width:23px;height:23px;border:1px solid var(--gold);display:flex;align-items:center;justify-content:center}
.header-cta{position:absolute;left:833px;top:15px;width:113px;height:26px;background:var(--gold);color:var(--white);font-size:7.5px;font-weight:700;letter-spacing:.8px;display:flex;align-items:center;justify-content:center}

/* hero */
.hero{position:absolute;left:0;top:57px;width:1088px;height:381px;background:var(--hero-bg)}
.hero-photo{position:absolute;left:0;top:0}
.hero-title{position:absolute;left:145px;top:66px;font-size:28px;font-weight:700;letter-spacing:2.5px;line-height:1}
.hero-title span,.section-title span{color:var(--gold-text)}
.hero-sub{position:absolute;left:145px;top:100px;font-size:14px;letter-spacing:.9px;color:#333}
.hero-text{position:absolute;left:145px;top:127px;width:515px;font-size:10px;line-height:15.4px;letter-spacing:.35px;color:var(--grey)}
.btn{position:absolute;height:34px;display:flex;align-items:center;justify-content:center;font-size:9.4px;letter-spacing:.6px}
.btn-primary{left:145px;top:217px;width:142px;background:var(--gold);color:var(--white)}
.btn-outline{left:320px;top:217px;width:116px;border:1px solid var(--gold);color:#333;background:var(--white)}

/* search */
.search-band{position:absolute;left:142px;top:381px;width:804px;height:114px;background:var(--gold);box-shadow:0 8px 18px rgba(0,0,0,.12);z-index:2}
.field{position:absolute;top:40px;width:170px;height:34px;background:var(--white);border:1px solid #e6d6ad;display:flex;align-items:center;justify-content:space-between;padding:0 10px 0 12px;font-size:9.4px;color:#777}
.search-btn{position:absolute;left:657px;top:40px;width:114px;height:34px;background:var(--dark);color:var(--white);font-size:7.5px;font-weight:700;letter-spacing:.7px;display:flex;align-items:center;justify-content:center}

/* branches */
.section-title{position:absolute;left:0;width:1088px;top:544px;text-align:center;font-size:26px;font-weight:700;letter-spacing:3.5px}
.section-sub{position:absolute;left:0;width:1100px;top:578px;text-align:center;font-size:12.5px;letter-spacing:1.6px;color:#333}
.card{position:absolute;width:138px;height:141px;background:var(--gold-soft);display:flex;flex-direction:column;align-items:center;box-shadow:0 2px 6px rgba(0,0,0,.05)}
.card.active{background:var(--card-active);border:1px solid #d9c694}
.card svg{margin-top:30px}
.card-name{margin-top:14px;font-size:14.5px;font-weight:500;letter-spacing:1.1px}
.card-count{margin-top:2px;font-size:8px;letter-spacing:.9px;color:#555}

/* footer */
.site-footer{position:absolute;left:0;top:1027px;width:1088px;height:173px;background:linear-gradient(#555,#222);color:var(--white)}
.footer-mark{position:absolute;left:240px;top:41px;width:56px;height:56px;border-radius:50%;border:2px solid var(--white)}
.footer-title{position:absolute;top:41px;font-size:10px;font-weight:700;letter-spacing:.6px}
.footer-text{position:absolute;left:325px;top:66px;width:170px;font-size:8.8px;line-height:14px}
.footer-link{position:absolute;font-size:8.8px}
.footer-link.underline{text-decoration:underline}
</style>
</head>
<body>

<header class="site-header">
  <div class="brand"><span class="brand-dot"></span>Wir-bauen-Brücken</div>
  <nav class="nav">
    <a class="active" style="left:261px">HOME</a>
    <a style="left:329px">SUCHEN</a>
    <a style="left:408px">ÜBER UNS</a>
    <a style="left:493px">MITGLIEDSCHAFT</a>
    <a style="left:612px">KONTAKT</a>
  </nav>
  <div class="icon-box" style="left:747px">
    <svg width="16" height="11" viewBox="0 0 16 11"><rect width="16" height="3.7" fill="#111"/><rect y="3.7" width="16" height="3.6" fill="#d00"/><rect y="7.3" width="16" height="3.7" fill="#fc0"/></svg>
  </div>
  <div class="icon-box" style="left:777px">
    <svg width="12" height="12" viewBox="0 0 12 12"><circle cx="6" cy="3.5" r="2.7" fill="#d5b062"/><path d="M1 12c0-3.3 2.2-5 5-5s5 1.7 5 5z" fill="#d5b062"/></svg>
  </div>
  <div class="header-cta">MITGLIED WERDEN</div>
</header>

<section class="hero">
  <svg class="hero-photo" width="1088" height="381" viewBox="0 0 1088 381">
    <defs>
      <linearGradient id="photoTone" x1="0" y1="0" x2="0" y2="1">
        <stop offset="0" stop-color="#f4f4f4"/>
        <stop offset=".55" stop-color="#c9ccce"/>
        <stop offset="1" stop-color="#8e8a86"/>
      </linearGradient>
    </defs>
    <path d="M815 0 C735 70 720 210 795 381 L1088 381 L1088 0 Z" fill="#d5b062"/>
    <path d="M822 0 C745 70 732 210 802 381 L1088 381 L1088 0 Z" fill="#fff7df"/>
    <path d="M828 0 C752 70 740 210 808 381 L1088 381 L1088 0 Z" fill="url(#photoTone)" role="img" aria-label="Foto: zwei Personen sitzen auf einem Holzsteg am See"/>
  </svg>
  <h1 class="hero-title">WIR BAUEN <span>BRÜCKEN</span></h1>
  <p class="hero-sub">Das Branchenverzeichnis der Selbstverantwortlichen</p>
  <p class="hero-text">Lorem ipsum dolor sit amet, consectetur adipisicing elit, sed do eiusmod tempor incididunt ut labore et dolore magna aliqua. Duis aute irure dolor in reprehenderit in voluptate velit esse cillum dolore eu fugiat nulla pariatur. Ut enim ad minim veniam, quis nostrud exercitation ullamco laboris nisi ut aliquip ex ea commodo!</p>
  <div class="btn btn-primary">UNTERNEHMER SUCHEN</div>
  <div class="btn btn-outline">MITGLIED WERDEN</div>
</section>

<div class="search-band">
  <div class="field" style="left:34px">Unternehmen, Name
    <svg width="16" height="14" viewBox="0 0 16 14"><path d="M8 0 0 7h2v7h4.5V9.5h3V14H14V7h2z" fill="#d5b062"/></svg>
  </div>
  <div class="field" style="left:232px">Stadt, PLZ oder Land
    <svg width="16" height="16" viewBox="0 0 16 16"><circle cx="8" cy="8" r="5.5" fill="none" stroke="#d5b062" stroke-width="1.5"/><circle cx="8" cy="8" r="2.5" fill="#d5b062"/><path d="M8 0v2.5M8 13.5V16M0 8h2.5M13.5 8H16" stroke="#d5b062" stroke-width="1.5"/></svg>
  </div>
  <div class="field" style="left:430px">Branche
    <svg width="12" height="8" viewBox="0 0 12 8"><path d="M1 1l5 5 5-5" fill="none" stroke="#d5b062" stroke-width="1.6"/></svg>
  </div>
  <div class="search-btn">SUCHEN</div>
</div>

<h2 class="section-title">WIR BAUEN <span>BRANCHEN</span></h2>
<p class="section-sub">Top 10 der gesuchten Unternehmenszweige.</p>

<svg width="0" height="0" style="position:absolute">
  <symbol id="people" viewBox="0 0 58 36">
    <circle cx="18" cy="8" r="8"/><circle cx="40" cy="8" r="7.5"/>
    <path d="M0 36c0-9 7-16 18-16s18 7 18 16z"/>
    <path d="M34 21c2-2 4-3 7-3 9 0 16 7 17 18H39c0-6-2-11-5-15z"/>
  </symbol>
</svg>

<div class="card" style="left:148px;top:636px"><svg width="57" height="36" fill="#fff"><use href="#people"/></svg><div class="card-name">Coaching</div><div class="card-count">(23 Unternehmen)</div></div>
<div class="card active" style="left:314px;top:636px"><svg width="57" height="36" fill="#d5b062"><use href="#people"/></svg><div class="card-name">Consulting</div><div class="card-count">(14 Unternehmen)</div></div>
<div class="card" style="left:481px;top:636px"><svg width="57" height="36" fill="#fff"><use href="#people"/></svg><div class="card-name">IT &amp; Marketing</div><div class="card-count">(23 Unternehmen)</div></div>
<div class="card" style="left:647px;top:636px"><svg width="57" height="36" fill="#fff"><use href="#people"/></svg><div class="card-name">Logistik</div><div class="card-count">(23 Unternehmen)</div></div>
<div class="card" style="left:814px;top:636px"><svg width="57" height="36" fill="#fff"><use href="#people"/></svg><div class="card-name">Bildung</div><div class="card-count">(23 Unternehmen)</div></div>

<div class="card" style="left:148px;top:822px"><svg width="57" height="36" fill="#fff"><use href="#people"/></svg><div class="card-name">Coaching</div><div class="card-count">(23 Unternehmen)</div></div>
<div class="card" style="left:314px;top:822px"><svg width="57" height="36" fill="#fff"><use href="#people"/></svg><div class="card-name">Coaching</div><div class="card-count">(23 Unternehmen)</div></div>
<div class="card" style="left:481px;top:822px"><svg width="57" height="36" fill="#fff"><use href="#people"/></svg><div class="card-name">IT &amp; Marketing</div><div class="card-count">(23 Unternehmen)</div></div>
<div class="card" style="left:647px;top:822px"><svg width="57" height="36" fill="#fff"><use href="#people"/></svg><div class="card-name">Logistik</div><div class="card-count">(23 Unternehmen)</div></div>
<div class="card" style="left:814px;top:822px"><svg width="57" height="36" fill="#fff"><use href="#people"/></svg><div class="card-name">Bildung</div><div class="card-count">(23 Unternehmen)</div></div>

<footer class="site-footer">
  <div class="footer-mark"></div>
  <div class="footer-title" style="left:325px">WIR BAUEN BRÜCKEN</div>
  <p class="footer-text">Duis sed odio sit amet nibh vulputate cursus a sit amet mauris Morbi accu.</p>
  <div class="footer-link underline" style="left:325px;top:110px">Über uns</div>

  <div class="footer-title" style="left:587px">WEBSITE</div>
  <div class="footer-link" style="left:587px;top:66px">Unternehmen suchen</div>
  <div class="footer-link" style="left:587px;top:85px">Mitgliedschaft</div>
  <div class="footer-link" style="left:587px;top:104px">Kontakt</div>

  <div class="footer-title" style="left:760px">RECHTLICHES</div>
  <div class="footer-link" style="left:760px;top:66px">Impressum</div>
  <div class="footer-link" style="left:760px;top:85px">Datenschutz</div>
  <div class="footer-link" style="left:760px;top:104px">AGB</div>
</footer>

</body>
</html>
```